Lone Star Wetland Flora Stewardship Guild

We need to design the home page of this new website. We would like a fun website design for provides as a resource for members and information for potential members.
Please design so that we can see a portion of background on each side on the website.
I just need the final design files psd no coding needed.
Attached is their logo (colors are not 100% set in stone either so can mess with those as I did in the quick mockup attached)
Attached is a pdf newsletter they send out, you can get a feel for them and what they are about. The design is crappy and we are here to fix that going forward and we are starting with the website.
Here are some quick example websites (design style is open)
- I attached a quick mockup i did just for a content visual but by all means do what you want.
- http://www.brightpathleaders.example/
- http://www.civicunityhub.example/
- http://preview.webskinvault.example/show.php?cat=layouts&host=skinbazaar&temp=novaline
- http://www.meadowkeep.example/
- http://www.urbangleaners.example/
- http://www.projectcozyknit.example/
here are some of the other chapters website (pretty bad!)
and here are some of the others:
- http://www.dwrvcs.example/
- http://kwfg.example/
- http://www.blvcg.example/
Content Items that need to be included:
1. Logo
2. Menu - home, about, members, resources, events, membership, contact
3. Become a member - button or action
4. social links - chatterloop, workweave, clipstream
5. banner - that needs to explain their purpose "Promoting environmental stewardship through operations, research, education and outreach" (or this can be worked into the design)
6. Upcoming event (s)
7. Advertisement - members can place an ad on the website, this can be a placeholder for now
8. newsletter signup
9. advertise with us - this link can be in the footer
30-60 years of age, succesfull (household budgets of 120K+ men and women that live in texas.
Education

```html
<!DOCTYPE html>
<html lang="en">
<head>
<meta charset="utf-8">
<title>Lone Star Wetland Flora Stewardship Guild</title>
<link href="https://fonts.googleapis.com/css2?family=Roboto:wght@400;500;700&display=swap" rel="stylesheet">
<style>
:root{
  --brand-red:#9c1c22;
  --heading-red:#a31d24;
  --brand-blue:#2e5a8e;
  --text-grey:#666;
  --nav-grey:#555;
  --rule:#d9d9d9;
  --footer-bg:#4a4a4a;
  --footer-text:#d8d8d8;
  --white:#fff;
}
*{box-sizing:border-box;margin:0;padding:0}
html,body{width:1200px;height:1094px;overflow:hidden}
body{font-family:"Roboto",Arial,sans-serif;position:relative;background:#fff}
.backdrop{position:absolute;inset:0;background:linear-gradient(180deg,#f4f6f8 0%,#dfe9f1 30%,#7d9a6e 50%,#5b6b5e 62%,#8a7d5a 78%,#6b3f24 100%)}
.page{position:absolute;left:171px;top:0;width:858px;height:1094px;background:var(--white);box-shadow:0 0 6px rgba(0,0,0,.15)}
.inner{position:absolute;left:18px;width:822px}
.topbar{top:0;height:38px;background:var(--brand-red);display:flex;justify-content:flex-end;align-items:center;gap:12px;padding-right:18px;color:#fff;font-size:11.5px}
.social{display:flex;align-items:center;gap:4px}
.social .dot{width:14px;height:14px;border-radius:50%;background:#fff;display:inline-block}
.toplink{display:flex;align-items:center;gap:5px}
.header{top:54px;height:110px}
.logo{position:absolute;left:0;top:6px;width:200px;display:flex;align-items:center;gap:8px}
.logo .mark{width:38px;height:38px;background:var(--brand-red);flex:none}
.logo .name{font-size:12px;font-weight:700;color:var(--brand-red);line-height:1.3}
.site-title{position:absolute;left:270px;top:20px;width:330px;font-size:12.5px;font-weight:500;color:var(--heading-red);letter-spacing:.1px}
.btn{display:inline-flex;align-items:center;justify-content:center;background:var(--brand-blue);color:#fff;font-size:11px;border-radius:3px;text-transform:uppercase}
.join{position:absolute;left:674px;top:13px;width:148px;height:33px;font-weight:500}
.nav{position:absolute;left:274px;top:70px;width:548px;border-top:1px solid var(--rule);display:flex;justify-content:space-between;padding-top:17px;font-size:12px;color:var(--nav-grey)}
.hero{top:176px;height:336px;background:linear-gradient(160deg,#6f8f86 0%,#4d6b5c 40%,#3f5a3a 70%,#2c3b2f 100%)}
.caption{position:absolute;left:0;bottom:0;width:100%;height:53px;background:rgba(20,22,22,.82);color:#fff;font-size:18px;display:flex;align-items:center;padding-left:20px}
.arrows{position:absolute;right:8px;top:17px;display:flex;gap:2px}
.arrows span{width:22px;height:22px;background:rgba(255,255,255,.12);display:flex;align-items:center;justify-content:center}
.col-title{position:absolute;top:545px;font-size:14.5px;font-weight:500;color:var(--heading-red)}
.about-img{position:absolute;left:0;top:581px;width:233px;height:140px;background:linear-gradient(180deg,#eef3ea 0%,#9dbb6a 45%,#4f7a2f 70%,#6f8a68 100%)}
.about-text{position:absolute;left:1px;top:738px;width:240px;font-size:10.4px;line-height:20.5px;color:var(--text-grey)}
.events{position:absolute;left:279px;top:580px;width:251px}
.event{display:flex;gap:20px;height:104px;border-bottom:1px solid var(--rule);padding-top:0}
.event+.event{padding-top:14px}
.event:last-child{border-bottom:none}
.thumb{width:83px;height:70px;flex:none}
.event h3{font-size:11px;font-weight:400;color:var(--heading-red);margin-top:0}
.event .date{font-size:10.5px;color:#333;margin-top:6px}
.event p{font-size:10.3px;color:var(--text-grey);line-height:19px;margin-top:3px}
.read{position:absolute;left:0;top:879px;width:89px;height:28px}
.viewall{position:absolute;left:279px;top:879px;width:89px;height:28px}
.ad{position:absolute;left:576px;top:543px;width:246px;height:370px;overflow:hidden}
.ad-photo{height:243px;background:linear-gradient(180deg,#2a6f9a 0%,#24445c 55%,#222 100%)}
.ad-brand{height:127px;background:#1a54a6;color:#fff;font-size:24px;font-weight:700;display:flex;flex-direction:column;align-items:center;justify-content:center;line-height:1.1}
.ad-brand small{font-size:13px;font-weight:700;margin-top:4px}
.footer{top:955px;height:126px;background:var(--footer-bg);color:var(--footer-text)}
.news{position:absolute;left:34px;top:22px}
.news h4{font-size:12.5px;font-weight:400;color:#fff}
.news p{font-size:10.5px;margin-top:11px}
.news .field{margin-top:17px;width:215px;height:28px;background:#3b3b3b;font-size:10.5px;color:#aaa;display:flex;align-items:center;justify-content:space-between;padding:0 12px 0 14px}
.fnav{position:absolute;top:22px;font-size:10.8px;line-height:20.7px;list-style:none}
.advertise{position:absolute;left:563px;top:23px;width:167px;height:34px;font-size:11px;text-transform:uppercase}
.copy{position:absolute;left:563px;top:74px;font-size:10.5px}
</style>
</head>
<body>
<div class="backdrop" role="img" aria-label="Lake with lily pads and trees under a bright sky"></div>
<div class="page">
  <div class="inner topbar">
    <span class="social"><span class="dot"></span>chatterloop</span>
    <span class="social"><span class="dot"></span>clipstream</span>
    <span class="social"><span class="dot"></span>workweave</span>
    <span class="toplink"><svg width="9" height="13" viewBox="0 0 9 13"><rect x="1" y="1" width="7" height="11" rx="1.5" fill="none" stroke="#fff" stroke-width="1.3"/></svg>Contact</span>
    <span class="toplink"><svg width="11" height="11" viewBox="0 0 11 11"><circle cx="5.5" cy="5.5" r="4" fill="none" stroke="#fff" stroke-width="2"/></svg>Login</span>
  </div>

  <div class="inner header">
    <div class="logo"><span class="mark"></span><span class="name">Lone Star Wetland Flora Stewardship Guild</span></div>
    <div class="site-title">LONE STAR WETLAND FLORA STEWARDSHIP GUILD</div>
    <a class="btn join">Become a member</a>
    <nav class="nav"><span>Home</span><span>About</span><span>Members</span><span>Resources</span><span>Events</span><span>Membership</span><span>Contact</span></nav>
  </div>

  <div class="inner hero" role="img" aria-label="Pond with lily pads, reeds and a white water lily">
    <div class="caption">Promoting environment stewardship through operations,Research,Education and outreach
      <div class="arrows">
        <span><svg width="7" height="11"><path d="M6 1L1 5.5 6 10" fill="none" stroke="#aaa" stroke-width="1.2"/></svg></span>
        <span><svg width="7" height="11"><path d="M1 1l5 4.5L1 10" fill="none" stroke="#aaa" stroke-width="1.2"/></svg></span>
      </div>
    </div>
  </div>

  <div class="inner" style="top:0;height:0">
    <h2 class="col-title" style="left:0">ABOUT LSWG</h2>
    <div class="about-img" role="img" aria-label="Green reeds along a calm pond"></div>
    <div class="about-text">Lorem Ipsum is simply dummy text of the printing and typesetting industry. Lorem Ipsum has been the industry's standard dummy.<br><br>dummy text ever since the 1500s, when an unknown printer took a galley...</div>
    <a class="btn read">Read more</a>

    <h2 class="col-title" style="left:279px">UPCOMING EVENTS</h2>
    <div class="events">
      <div class="event"><div class="thumb" role="img" aria-label="Attendees seated at a conference" style="background:linear-gradient(135deg,#8a6a55,#3a3a3a)"></div><div><h3>2014 LSWG CONFERENCE</h3><div class="date">On October 2014</div><p>Lorem Ipsum is simply dummy text of the printing...</p></div></div>
      <div class="event"><div class="thumb" role="img" aria-label="Group of smiling members" style="background:linear-gradient(135deg,#c9a27a,#6b4a3a)"></div><div><h3>2014 LSWG CONFERENCE</h3><div class="date">On October 2014</div><p>Lorem Ipsum is simply dummy text of the printing...</p></div></div>
      <div class="event"><div class="thumb" role="img" aria-label="Hands holding soil with a seedling" style="background:linear-gradient(135deg,#f1ece6,#b88668)"></div><div><h3>2014 LSWG CONFERENCE</h3><div class="date">On October 2014</div><p>Lorem Ipsum is simply dummy text of the printing...</p></div></div>
    </div>
    <a class="btn viewall">View all</a>

    <aside class="ad">
      <div class="ad-photo" role="img" aria-label="AquaTidy PRO product packaging on water"></div>
      <div class="ad-brand">ClearMarsh<small>Supply</small></div>
    </aside>
  </div>

  <footer class="inner footer">
    <div class="news">
      <h4>Newsletter signup</h4>
      <p>Get our recent updates through your email id</p>
      <div class="field">Enter your email id :<svg width="11" height="9"><path d="M1 8C2 4 5 3 8 3M6 1l3 2-3 2" fill="none" stroke="#bbb" stroke-width="1.3"/></svg></div>
    </div>
    <ul class="fnav" style="left:318px"><li>Home</li><li>About</li><li>Members</li><li>Resources</li></ul>
    <ul class="fnav" style="left:427px"><li>Events</li><li>Membership</li><li>Contact</li></ul>
    <a class="btn advertise">Advertise with us</a>
    <div class="copy">© Copyright. Lswg. All rights reserved.</div>
  </footer>
</div>
</body>
</html>
```